Velmora Cabinets Letter Head and Email Signature

Hi
I would love a design package for a letterhead, email signature, even update my business card if you like if you can come up with a great idea for my new high end cabinet shop. Velmora Cabinets brings timeless craftsmanship to modern interiors, specializing in high end, custom cabinetry designed for architects and interior designers.

Target Market(s)

high end, luxury market

Industry/Entity Type

cabinet making

Requirements
Must have
• my colours of logo as the theme

```html
<!DOCTYPE html>
<html lang="en">
<head>
<meta charset="utf-8">
<title>Velmora Cabinets Stationery</title>
<link href="https://fonts.googleapis.com/css2?family=Montserrat:wght@400;500;600&family=Lexend:wght@400;500&display=swap" rel="stylesheet">
<style>
:root{
  --green:#4f7f45;
  --green-faint:#cfd8c8;
  --ink:#0a0b0c;
  --paper:#ffffff;
  --stage:#5b3820;
  --label:#f3ece4;
  --text:#1c1c1c;
}
*{margin:0;padding:0;box-sizing:border-box}
html,body{width:1200px;height:1070px;overflow:hidden}
body{background:var(--stage);font-family:"Montserrat",sans-serif;color:var(--text);position:relative}
.piece{position:absolute;background:var(--paper);overflow:hidden}
.label{position:absolute;color:var(--label);font-size:13px;font-weight:400;letter-spacing:.2px}
.abs{position:absolute}
.brand{display:flex;align-items:center;gap:10px;font-family:"Lexend",sans-serif;font-weight:400;color:var(--green);white-space:nowrap}
.brand .wm{display:block;line-height:1.08}
.brand .sq{border:2px solid var(--green);flex:none}
.contact{display:flex;align-items:center;gap:6px;white-space:nowrap}
.ico{width:1.25em;height:1.25em;flex:none;color:var(--green)}
.name{font-family:"Lexend",sans-serif;color:var(--green);font-weight:500;white-space:nowrap}
.role{font-weight:500;white-space:nowrap}
.tag{color:var(--green)}

/* letterhead */
.letterhead{left:56px;top:51px;width:570px;height:738px}
.letterhead .brand{left:20px;top:14px;font-size:20px}
.letterhead .brand .sq{width:40px;height:40px}
.letterhead .motto{right:16px;top:20px;text-align:right;font-size:10.5px;font-weight:600;line-height:16px;letter-spacing:.3px}
.letterhead .bar{right:0;top:24px;width:2px;height:26px;background:var(--green)}
.letterhead .rule-g{left:0;top:70px;width:403px;height:1.5px;background:var(--green)}
.letterhead .rule-k{left:408px;top:70px;width:162px;height:1.5px;background:var(--ink)}
.letterhead .watermark{right:36px;top:590px;font-family:"Lexend",sans-serif;font-size:34px;line-height:1.1;color:var(--green-faint);text-align:right}
.letterhead .foot{left:0;bottom:0;width:100%;height:44px;background:var(--ink);border-top:2px solid var(--green);display:flex;align-items:center;color:#fff;font-size:11px}
.letterhead .foot .contact{position:absolute}

/* business cards */
.card{left:769px;width:281px;height:160px}
.card.front{top:73px}
.card.front .name{left:15px;top:18px;font-size:12px}
.card.front .role{left:15px;top:34px;font-size:6.5px}
.card.front .list{left:15px;top:60px;font-size:8px;display:flex;flex-direction:column;gap:9px}
.card.front .tag{left:15px;top:129px;font-size:8px}
.card.front .sq-mark{left:198px;top:80px;width:54px;height:54px;border:3px solid var(--ink)}
.card.dark{background:var(--ink);display:flex;flex-direction:column;align-items:center;justify-content:center}
.card.dark.logo-only{top:250px}
.card.dark.with-tag{top:426px}
.card.dark .brand{font-size:23px}
.card.dark .brand .sq{width:46px;height:46px;border-color:#fff}
.card.dark .tag-w{color:#fff;font-size:10px;margin-top:20px}

/* email signature 2 */
.sig2{left:664px;top:606px;width:454px;height:160px}
.sig2 .side{left:0;top:0;width:174px;height:100%;background:var(--ink)}
.sig2 .side .brand{position:absolute;left:14px;top:20px;font-size:17px}
.sig2 .side .brand .sq{width:36px;height:36px;border-color:#fff}
.sig2 .name{left:195px;top:18px;font-size:11.5px}
.sig2 .role{left:195px;top:34px;font-size:6.5px}
.sig2 .list{left:195px;top:61px;font-size:8px;display:flex;flex-direction:column;gap:9px}
.sig2 .sq-mark{left:362px;top:30px;width:62px;height:62px;border:3px solid var(--ink)}
.sig2 .rule{left:174px;top:122px;width:280px;height:1px;background:var(--green)}
.sig2 .tag-k{left:195px;top:136px;font-size:8px}

/* email signature 1 */
.sig1{left:63px;top:826px;width:454px;height:181px}
.sig1 .brand{left:13px;top:13px;font-size:16px}
.sig1 .brand .sq{width:34px;height:34px}
.sig1 .who{left:13px;top:99px;font-size:11.5px;white-space:nowrap}
.sig1 .who .role{font-family:"Montserrat",sans-serif;color:var(--text);font-size:7.5px}
.sig1 .row{left:13px;top:124px;font-size:8.5px;display:flex;gap:32px}
.sig1 .band{left:0;bottom:0;width:100%;height:30px;background:var(--ink);color:#fff;font-size:8px;letter-spacing:1.3px;padding:10px 13px;font-weight:500}

/* email signature 3 */
.sig3{left:557px;top:839px;width:601px;height:168px}
.sig3 .brand{left:20px;top:32px;font-size:22px}
.sig3 .brand .sq{width:46px;height:46px}
.sig3 .tag-k{left:20px;top:124px;font-size:10.5px}
.sig3 .divider{left:229px;top:40px;width:1px;height:78px;background:#d8d8d8}
.sig3 .name{left:248px;top:32px;font-size:15px}
.sig3 .role{left:248px;top:53px;font-size:8.5px}
.sig3 .rule1{left:248px;top:73px;width:334px;height:1px;background:#d8d8d8}
.sig3 .row{left:248px;top:83px;font-size:8.5px;display:flex;gap:12px}
.sig3 .rule2{left:248px;top:106px;width:334px;height:1px;background:#d8d8d8}
.sig3 .socials{left:248px;top:117px;font-size:10px;font-weight:500;display:flex;gap:10px;align-items:center}
.sig3 .socials .sep{width:1px;height:14px;background:#cfcfcf}
.sig3 .dot{width:15px;height:15px;border:1px solid var(--green);border-radius:50%;flex:none}
</style>
</head>
<body>

<svg width="0" height="0" style="position:absolute" aria-hidden="true">
  <defs>
    <symbol id="ico-phone" viewBox="0 0 20 20">
      <circle cx="10" cy="10" r="9" fill="none" stroke="currentColor" stroke-width="1.4"/>
      <path d="M7 5.5l2 2.4-1.2 1.2c.6 1.4 1.6 2.4 3 3l1.2-1.2 2.4 2-1.2 1.6c-3.8-.4-7-3.6-7.4-7.4z" fill="currentColor"/>
    </symbol>
    <symbol id="ico-mail" viewBox="0 0 20 20">
      <path d="M2 8l8-5 8 5v9H2z" fill="currentColor"/>
      <path d="M2 8l8 5 8-5" fill="none" stroke="#fff" stroke-width="1.2"/>
    </symbol>
    <symbol id="ico-handle" viewBox="0 0 20 20">
      <rect x="2.5" y="2.5" width="15" height="15" rx="3" fill="none" stroke="currentColor" stroke-width="1.6"/>
    </symbol>
  </defs>
</svg>

<!-- Letterhead -->
<section class="piece letterhead">
  <div class="abs brand"><span class="sq"></span><span class="wm">Velmora<br>Cabinets</span></div>
  <p class="abs motto">REFINED CRAFTMANSHIP,<br>LUXURY BEAUTY</p>
  <span class="abs bar"></span>
  <span class="abs rule-g"></span>
  <span class="abs rule-k"></span>
  <div class="abs watermark">Velmora<br>Cabinets</div>
  <footer class="abs foot">
    <span class="contact" style="left:57px"><svg class="ico"><use href="#ico-phone"/></svg>0400 318 562</span>
    <span class="contact" style="left:191px"><svg class="ico"><use href="#ico-mail"/></svg>info@velmoracabinets.com.au</span>
    <span class="contact" style="left:397px"><svg class="ico"><use href="#ico-handle"/></svg>@velmora.cabinets</span>
  </footer>
</section>

<!-- Business cards -->
<p class="label" style="left:967px;top:44px">Business Card</p>

<section class="piece card front">
  <p class="abs name">Elias Marten</p>
  <p class="abs role">Director Craftsman</p>
  <div class="abs list">
    <span class="contact"><svg class="ico"><use href="#ico-phone"/></svg>0400 318 562</span>
    <span class="contact"><svg class="ico"><use href="#ico-mail"/></svg>info@velmoracabinets.com.au</span>
    <span class="contact"><svg class="ico"><use href="#ico-handle"/></svg>@velmora.cabinets</span>
  </div>
  <p class="abs tag">Refined Craftmanship, Luxury Beauty</p>
  <span class="abs sq-mark"></span>
</section>

<section class="piece card dark logo-only">
  <div class="brand"><span class="sq"></span><span class="wm">Velmora<br>Cabinets</span></div>
</section>

<section class="piece card dark with-tag">
  <div class="brand"><span class="sq"></span><span class="wm">Velmora<br>Cabinets</span></div>
  <p class="tag-w">Refined Craftmanship, Luxury Beauty</p>
</section>

<!-- Email signature 2 -->
<section class="piece sig2">
  <div class="abs side"><div class="brand"><span class="sq"></span><span class="wm">Velmora<br>Cabinets</span></div></div>
  <p class="abs name">Elias Marten</p>
  <p class="abs role">Director Craftsman</p>
  <div class="abs list">
    <span class="contact"><svg class="ico"><use href="#ico-phone"/></svg>0400 318 562</span>
    <span class="contact"><svg class="ico"><use href="#ico-mail"/></svg>info@velmoracabinets.com.au</span>
    <span class="contact"><svg class="ico"><use href="#ico-handle"/></svg>@velmora.cabinets</span>
  </div>
  <span class="abs sq-mark"></span>
  <span class="abs rule"></span>
  <p class="abs tag-k">Refined Craftmanship, Luxury Beauty</p>
</section>
<p class="label" style="left:664px;top:774px">Email Signature Option 2</p>

<!-- Email signature 1 -->
<section class="piece sig1">
  <div class="abs brand"><span class="sq"></span><span class="wm">Velmora<br>Cabinets</span></div>
  <p class="abs who"><span class="name">Elias Marten,</span> <span class="role">Director Craftsman</span></p>
  <div class="abs row">
    <span class="contact"><svg class="ico"><use href="#ico-phone"/></svg>0400 318 562</span>
    <span class="contact"><svg class="ico"><use href="#ico-mail"/></svg>info@velmoracabinets.com.au</span>
    <span class="contact"><svg class="ico"><use href="#ico-handle"/></svg>@velmora.cabinets</span>
  </div>
  <p class="abs band">REFINED CRAFTMANSHIP, LUXURY BEAUTY</p>
</section>
<p class="label" style="left:63px;top:1016px">Email Signature Option 1</p>

<!-- Email signature 3 -->
<section class="piece sig3">
  <div class="abs brand"><span class="sq"></span><span class="wm">Velmora<br>Cabinets</span></div>
  <p class="abs tag-k">Refined Craftmanship, Luxury Beauty</p>
  <span class="abs divider"></span>
  <p class="abs name">Elias Marten</p>
  <p class="abs role">Director Craftsman</p>
  <span class="abs rule1"></span>
  <div class="abs row">
    <span class="contact"><svg class="ico"><use href="#ico-phone"/></svg>0400 318 562</span>
    <span class="contact"><svg class="ico"><use href="#ico-mail"/></svg>info@velmoracabinets.com.au</span>
    <span class="contact"><svg class="ico"><use href="#ico-handle"/></svg>@velmora.cabinets</span>
  </div>
  <span class="abs rule2"></span>
  <div class="abs socials">
    <span class="contact"><span class="dot"></span>Circleon</span><span class="sep"></span>
    <span class="contact"><span class="dot"></span>Workline</span><span class="sep"></span>
    <span class="contact"><span class="dot"></span>Pagebook</span><span class="sep"></span>
    <span class="contact"><span class="dot"></span>Snapgram</span>
  </div>
</section>
<p class="label" style="left:562px;top:1016px">Email Signature Option 3</p>

</body>
</html>
```